Keystone Trench Co Business Card*

Looking for a professional, clean and crisp business card

I am in the underground utilities industry and am just looking for a really impressive business card. I would like our card to be white with our symbol crisp and clear with it protruding. I also have a business partner that will require his name and info on the card once the design is set. I would like to have our website info on the card which is;
http://keystonetrenchco.example/

Contact Information for Business Card

Website, contact name, number and email

```html
<!DOCTYPE html>
<html lang="en">
<head>
<meta charset="utf-8">
<title>Keystone Trench Co Business Card</title>
<link href="https://fonts.googleapis.com/css2?family=Lato:wght@400;700&family=Roboto+Condensed:wght@700&display=swap" rel="stylesheet">
<style>
  :root {
    --ink-black: #141516;
    --brand-blue: #2d67a5;
    --link-blue: #2e6bb0;
    --paper: #ffffff;
    --mark-dark: #232323;
    --edge-grey: #9a9a9a;
    --canvas: #ffffff;
  }
  html, body {
    margin: 0;
    padding: 0;
    width: 1045px;
    height: 1200px;
    overflow: hidden;
    background: var(--canvas);
  }
  .canvas {
    position: relative;
    width: 1045px;
    height: 1200px;
  }
  .card {
    position: absolute;
    left: 0;
    width: 1027px;
    height: 577px;
    box-sizing: border-box;
    overflow: hidden;
  }
  .card-front {
    top: 0;
    background: var(--ink-black);
    border: 1px solid #3a3a3a;
  }
  .card-back {
    top: 603px;
    background: var(--paper);
    border: 1px solid var(--edge-grey);
  }
  .wordmark {
    position: absolute;
    margin: 0;
    font-family: "Roboto Condensed", "Arial Narrow", sans-serif;
    font-weight: 700;
    text-align: center;
    line-height: 1.02;
    letter-spacing: 1px;
  }
  .card-front .wordmark {
    left: 0;
    width: 1027px;
    top: 175px;
    font-size: 76px;
    color: var(--paper);
  }
  .front-url {
    position: absolute;
    left: 0;
    width: 1027px;
    top: 482px;
    margin: 0;
    text-align: center;
    font-family: "Lato", sans-serif;
    font-size: 33px;
    color: var(--link-blue);
  }
  .back-shapes {
    position: absolute;
    left: 0;
    top: 0;
  }
  .card-back .wordmark {
    left: 60px;
    width: 310px;
    top: 705px;
    top: 102px;
    font-size: 60px;
    color: var(--mark-dark);
  }
  .person-name {
    position: absolute;
    left: 56px;
    top: 343px;
    margin: 0;
    font-family: "Lato", sans-serif;
    font-weight: 700;
    font-size: 37px;
    color: var(--paper);
  }
  .company-name {
    position: absolute;
    right: 64px;
    top: 112px;
    margin: 0;
    font-family: "Roboto Condensed", "Arial Narrow", sans-serif;
    font-weight: 700;
    font-size: 45px;
    letter-spacing: 0.5px;
    color: var(--paper);
  }
  .contact-list {
    position: absolute;
    right: 66px;
    top: 350px;
    margin: 0;
    padding: 0;
    list-style: none;
    font-family: "Lato", sans-serif;
    font-size: 34px;
    color: var(--paper);
  }
  .contact-list li {
    display: flex;
    justify-content: flex-end;
    align-items: center;
    height: 51px;
  }
  .contact-list svg {
    width: 28px;
    height: 28px;
    margin-left: 14px;
    flex: none;
  }
</style>
</head>
<body>
<main class="canvas">

  <section class="card card-front" aria-label="Card front">
    <p class="wordmark">KEYSTONE<br>TRENCH CO</p>
    <p class="front-url">www.keystonetrenchco.example</p>
  </section>

  <section class="card card-back" aria-label="Card back">
    <svg class="back-shapes" width="1027" height="577" viewBox="0 0 1027 577" aria-hidden="true">
      <polygon points="497,0 1027,0 1027,577 338,577" fill="var(--brand-blue)"/>
      <polygon points="0,324 398,324 373,410 0,410" fill="var(--brand-blue)"/>
    </svg>

    <p class="wordmark">KEYSTONE<br>TRENCH CO</p>
    <p class="person-name">Person Name</p>

    <h1 class="company-name">KEYSTONE TRENCH CO</h1>

    <ul class="contact-list">
      <li>883-555-0142
        <svg viewBox="0 0 28 28" aria-hidden="true">
          <rect x="7" y="2" width="14" height="24" rx="3" fill="none" stroke="#fff" stroke-width="2.6"/>
          <circle cx="14" cy="21" r="1.6" fill="#fff"/>
        </svg>
      </li>
      <li>info@keystonetrenchco.example
        <svg viewBox="0 0 28 28" aria-hidden="true">
          <rect x="2" y="6" width="24" height="16" rx="1.5" fill="#fff"/>
          <polyline points="3,7 14,16 25,7" fill="none" stroke="var(--brand-blue)" stroke-width="2"/>
          <polyline points="3,21 11,14 M25,21 17,14" fill="none" stroke="var(--brand-blue)" stroke-width="1.6"/>
        </svg>
      </li>
      <li>www.keystonetrenchco.example
        <svg viewBox="0 0 28 28" aria-hidden="true">
          <circle cx="14" cy="14" r="11" fill="none" stroke="#fff" stroke-width="2.4"/>
          <ellipse cx="14" cy="14" rx="5" ry="11" fill="none" stroke="#fff" stroke-width="2"/>
          <line x1="3" y1="14" x2="25" y2="14" stroke="#fff" stroke-width="2"/>
          <line x1="5" y1="8.5" x2="23" y2="8.5" stroke="#fff" stroke-width="1.6"/>
          <line x1="5" y1="19.5" x2="23" y2="19.5" stroke="#fff" stroke-width="1.6"/>
        </svg>
      </li>
    </ul>
  </section>

</main>
</body>
</html>
```